DESKHAVEN COSPACE Website design and coding

DESKHAVEN COSPACE

DESKHAVEN is Galveston’s first (and currently only) shared business co-working space. We share the same upscale, casual work environment, but we work independently on our own (or our team’s) projects and goals. For only a flat $195 membership fee per month, you have your very own all-inclusive, fun, personal business office environment. Website is written (Word file #12, below); and all pictures etc provided. Galveston is a beachy, coastal, historic city an hour from Houston, Texas USA. Logo (file 11 below) is temporary only.

Target Market(s)

Outside sales people, medical students looking for study hall, Houston companies looking for local office, real estate agents, graphic artists, entrepreneurs, etc

Contact Information for Business Card

will discuss --want to combine with current business card with multiple businesses

Logo Text

DESKHAVEN COSPACE

Coding

Coded - Design and coding required

Number of Pages Required

5+ page

Colors
ec1f27
fbed22

Requirements
Nice to have
• maroon/wine dominant with yellow and red accents, gray base are the colors of the space--website could coordinate--but open to creative ideas/combinations

```html
<!DOCTYPE html>
<html lang="en">
<head>
<meta charset="utf-8">
<title>DESKHAVEN COSPACE – Business Co-working Space</title>
<link rel="stylesheet" href="https://fonts.googleapis.com/css2?family=Exo+2:wght@300;400;600&family=Roboto:wght@400;500;700&display=swap">
<style>
:root{
  --red:#ec1f27;
  --yellow:#fbed22;
  --ink:#222;
  --text:#555;
  --white:#fff;
  --black:#0b0b0b;
  --head:"Exo 2",sans-serif;
  --body:"Roboto",sans-serif;
}
*{box-sizing:border-box;margin:0;padding:0}
html,body{width:1200px;height:4141px;overflow:hidden}
body{position:relative;font-family:var(--body);color:var(--ink);background:var(--white)}
.abs{position:absolute}

/* header */
.site-header{position:absolute;left:0;top:0;width:1200px;height:105px;background:rgba(20,18,12,.72);z-index:3}
.logo{position:absolute;left:62px;top:18px;font-family:var(--head);font-weight:400;color:var(--white);line-height:1}
.logo .l1{display:block;font-size:35px;letter-spacing:1px}
.logo .l2{display:block;font-size:24px;color:var(--yellow);margin:4px 0 0 20px;letter-spacing:1px}
.main-nav{position:absolute;left:322px;top:41px;display:flex;gap:38px;font-size:12px;font-weight:500;color:var(--white)}
.main-nav .active{color:var(--yellow)}
.phone{position:absolute;right:44px;top:36px;font-size:17px;font-weight:500;color:var(--white);display:flex;align-items:center;gap:7px}

/* hero */
.hero{position:absolute;left:0;top:0;width:1200px;height:780px;
  background:linear-gradient(160deg,#6b6140 0%,#4a422c 35%,#2a251b 70%,#3d3624 100%)}
.hero-cut{position:absolute;left:0;top:0}
.hero-title{position:absolute;left:0;width:1200px;top:286px;text-align:center;font-family:var(--head);font-weight:400;color:var(--white);font-size:62px;letter-spacing:2px}
.hero-sub{position:absolute;left:0;width:1200px;top:360px;text-align:center;font-family:var(--head);font-weight:300;color:var(--white);font-size:46px;letter-spacing:2px}
.btn{display:flex;align-items:center;justify-content:center;border-radius:30px;font-weight:700;letter-spacing:1.5px;background:var(--yellow);color:var(--ink)}
.hero .btn{position:absolute;left:495px;top:438px;width:200px;height:54px;font-size:16px;color:var(--red)}
.hero-arrow{position:absolute;left:584px;top:532px}
.hero-prev{position:absolute;left:74px;top:322px}
.hero-next{position:absolute;left:1114px;top:322px}

/* about */
.about-photo{position:absolute;left:116px;top:843px;width:405px;height:396px;border-radius:0 100px 0 120px;background:linear-gradient(135deg,#cfcbc2,#8a8478 50%,#3b3632)}
.about-inset{position:absolute;left:361px;top:1060px;width:196px;height:201px;border-radius:70px 60px 40px 0;background:linear-gradient(150deg,#c9c7b9,#8aa34a 50%,#d9cfc5);border:6px solid var(--white)}
.section-title{font-family:var(--head);font-weight:300;font-size:35px;letter-spacing:1.5px;line-height:1.2}
.section-title b{font-weight:400}
.about-title{position:absolute;left:646px;top:866px;color:var(--ink)}
.rule{position:absolute;height:3px;width:68px}
.about-text{position:absolute;left:646px;top:994px;width:460px;font-size:13px;line-height:27px;color:var(--text)}
.about .btn{position:absolute;left:642px;top:1163px;width:201px;height:54px;font-size:15px}

/* amenities */
.amenities{position:absolute;left:0;top:1354px;width:1200px;height:570px;background:var(--red);overflow:hidden}
.amenities-photo{position:absolute;left:0;top:0;width:1200px;height:570px;
  background:linear-gradient(90deg,var(--red) 0%,var(--red) 38%,#d2393a 52%,#a0633f 70%,#c79a55 85%,#e4c07a 100%)}
.amenities-title{position:absolute;left:106px;top:82px;font-family:var(--head);font-weight:400;font-size:33px;letter-spacing:2px;color:var(--white)}
.amenities .rule{left:106px;top:124px;background:var(--white);width:64px}
.amenities-text{position:absolute;left:106px;top:146px;width:480px;font-size:13px;line-height:26px;color:var(--white)}
.amenity{position:absolute;display:flex;align-items:center;gap:12px;color:var(--white);font-size:12.5px;line-height:19px;width:240px}
.amenity .dot{flex:none;width:64px;height:64px;border-radius:50%;background:var(--yellow);display:flex;align-items:center;justify-content:center}
.amenities .btn-outline{position:absolute;left:100px;top:417px;width:171px;height:45px;border:2px solid var(--yellow);border-radius:25px;color:var(--yellow);font-size:14px;font-weight:500;letter-spacing:1.5px;display:flex;align-items:center;justify-content:center}

/* philosophy */
.philosophy-title{position:absolute;left:0;width:1200px;top:2004px;text-align:center;color:var(--ink)}
.card{position:absolute;width:457px;height:202px;border:2px solid var(--red);padding:52px 30px 0 116px}
.card .icon{position:absolute;left:30px;top:46px;width:66px;height:66px;border:2px solid var(--red);border-radius:8px;background:#fde6e7}
.card h3{font-size:18px;font-weight:500;line-height:25px;color:var(--ink);margin-bottom:10px}
.card p{font-size:12.5px;line-height:19px;color:var(--text)}

/* gallery */
.gallery{position:absolute;left:0;top:2682px;width:1200px;height:694px;background:var(--yellow)}
.gallery-title{position:absolute;left:0;width:1200px;top:52px;text-align:center;color:var(--ink)}
.gallery .rule{left:563px;top:110px;background:var(--ink);width:74px}
.shot{position:absolute;width:318px;height:212px}

/* contact */
.contact-photo{position:absolute;left:0;top:3376px;width:594px;height:562px;background:linear-gradient(160deg,#e6e4df 0%,#a39d95 40%,#3e3a38 75%,#1e1c1c 100%)}
.contact{position:absolute;left:594px;top:3376px;width:606px;height:562px;background:var(--red)}
.contact-title{position:absolute;left:77px;top:74px;font-family:var(--head);font-weight:400;font-size:34px;letter-spacing:2px;color:var(--white)}
.contact .rule{left:77px;top:116px;background:var(--yellow);width:64px}
.field{position:absolute;left:81px;width:412px;height:45px;background:var(--white);font-size:12.5px;color:#666;padding:14px 20px}
.contact .btn{position:absolute;left:79px;top:424px;width:183px;height:48px;font-size:16px}

/* footer */
.site-footer{position:absolute;left:0;top:3938px;width:1200px;height:203px;background:var(--black);color:var(--white)}
.footer-nav{position:absolute;left:0;width:1200px;top:57px;display:flex;justify-content:center;gap:44px;font-size:13px;font-weight:500}
.copyright{position:absolute;left:0;width:1200px;top:92px;text-align:center;font-size:11.5px}
.social{position:absolute;left:0;width:1200px;top:133px;display:flex;justify-content:center;gap:10px}
.social span{width:30px;height:30px;border-radius:50%;background:var(--yellow)}
</style>
</head>
<body>

<section class="hero">
  <div class="abs" style="inset:0" role="img" aria-label="Photo of the co-working lounge with sofas and pendant lamps"></div>
  <svg class="hero-cut" width="1200" height="780" viewBox="0 0 1200 780"><polygon points="0,675 594,780 1200,675 1200,780 0,780" fill="#fff"/></svg>
  <svg class="hero-prev" width="30" height="48" viewBox="0 0 30 48"><polyline points="26,2 4,24 26,46" fill="none" stroke="#fff" stroke-width="3"/></svg>
  <svg class="hero-next" width="30" height="48" viewBox="0 0 30 48"><polyline points="4,2 26,24 4,46" fill="none" stroke="#fff" stroke-width="3"/></svg>
  <h1 class="hero-title">DESKHAVEN COSPACE</h1>
  <p class="hero-sub">BUSINESS CO-WORKING SPACE</p>
  <a class="btn">PLAY NOW</a>
  <svg class="hero-arrow" width="32" height="34" viewBox="0 0 32 34"><line x1="16" y1="2" x2="16" y2="30" stroke="#fff" stroke-width="3"/><polyline points="5,19 16,30 27,19" fill="none" stroke="#fff" stroke-width="3"/></svg>
</section>

<header class="site-header">
  <div class="logo"><span class="l1">DESKHAVEN</span><span class="l2">COSPACE</span></div>
  <nav class="main-nav"><span class="active">ABOUT</span><span>AMENITIES</span><span>MEMBERSHIP</span><span>PICTURES</span><span>THE DESKHAVEN PHILOSOPHY</span><span>CONTACT</span></nav>
  <div class="phone"><svg width="18" height="18" viewBox="0 0 24 24"><path d="M6.6 10.8a15 15 0 0 0 6.6 6.6l2.2-2.2a1 1 0 0 1 1-.25 11.4 11.4 0 0 0 3.6.57 1 1 0 0 1 1 1V20a1 1 0 0 1-1 1A17 17 0 0 1 3 4a1 1 0 0 1 1-1h3.5a1 1 0 0 1 1 1c0 1.25.2 2.45.57 3.57a1 1 0 0 1-.25 1z" fill="#fbed22"/></svg>555-014-2290</div>
</header>

<section class="about">
  <div class="about-photo" role="img" aria-label="Photo of the lounge with lockers, sofa and bar stools"></div>
  <div class="about-inset" role="img" aria-label="Photo of a potted plant and decorative vase"></div>
  <h2 class="section-title about-title">ABOUT <b>DESKHAVEN</b><br><b>COSPACE</b></h2>
  <div class="rule" style="left:646px;top:960px;background:var(--red)"></div>
  <p class="about-text">DESKHAVEN is Galveston’s first (and currently only) shared business co-working space. We share the same upscale, casual work environment, but we work independently on our own (or our team’s) projects and goals. For only a flat $195 membership fee per month, you have your very own all-inclusive, fun, personal business office environment.</p>
  <a class="btn">LEARN MORE</a>
</section>

<section class="amenities">
  <div class="amenities-photo" role="img" aria-label="Photo of the kitchen bar with long counter, stools and pendant lamps"></div>
  <h2 class="amenities-title">AMENITIES</h2>
  <div class="rule"></div>
  <p class="amenities-text">DESKHAVEN is the first Galveston co-working space, and offers all of the following features, all included in your monthly $195 membership fee:</p>
  <div class="amenity" style="left:101px;top:223px"><span class="dot" role="img" aria-label="Office desk icon"></span><span>Open office or a private cubicle for your daily use.</span></div>
  <div class="amenity" style="left:355px;top:223px"><span class="dot"><svg width="38" height="30" viewBox="0 0 38 30" fill="none" stroke="#222" stroke-width="3" stroke-linecap="round"><path d="M3 10a23 23 0 0 1 32 0"/><path d="M9 16a14 14 0 0 1 20 0"/><path d="M14.5 21.5a6 6 0 0 1 9 0"/><circle cx="19" cy="26" r="1.5" fill="#222"/></svg></span><span>24 hour access<br>&amp; Free WiFi</span></div>
  <div class="amenity" style="left:101px;top:308px"><span class="dot" role="img" aria-label="Coffee bar icon"></span><span>Communal coffee bar and kitchen, with FREE coffee</span></div>
  <div class="amenity" style="left:355px;top:308px"><span class="dot" role="img" aria-label="Networking people icon"></span><span>Great opportunity for networking or mentoring</span></div>
  <a class="btn-outline">LEARN MORE</a>
</section>

<section class="philosophy">
  <h2 class="section-title philosophy-title"><b>THE DESKHAVEN</b> PHILOSOPHY</h2>
  <div class="rule" style="left:565px;top:2056px;background:#d8c51c"></div>
  <article class="card" style="left:132px;top:2121px"><span class="icon" role="img" aria-label="Desk icon"></span><h3>WORK OUTSIDE THE HOME</h3><p>DESKHAVEN is the first Galveston co-working space, and offers all of the following features, all included in your monthly $195 membership fee:</p></article>
  <article class="card" style="left:609px;top:2121px"><span class="icon" role="img" aria-label="Trophy icon"></span><h3>DESKHAVEN THE COMPETITION</h3><p>Because of the flexibility, prestigious location, opportunities to meet and network with active professionals, and the available tech</p></article>
  <article class="card" style="left:132px;top:2341px;padding-top:42px"><span class="icon" role="img" aria-label="Coworkers icon"></span><h3>WORK IT OUT WITH YOUR COWORKERS</h3><p>DESKHAVEN is a community – if you are making a pot of (free) coffee – ask and make enough for everyone that wants some!</p></article>
  <article class="card" style="left:609px;top:2341px;padding-top:42px"><span class="icon" role="img" aria-label="Path to success icon"></span><h3>WORK OUT THE PATH TO YOUR SUCCESS</h3><p>As your business grows, there are other beautiful, “dedicated desk” private executive offices, and full office suites available in the building</p></article>
</section>

<section class="gallery">
  <h2 class="section-title gallery-title">OUR <b>GALLERY</b></h2>
  <div class="rule"></div>
  <div class="shot" style="left:108px;top:162px;background:linear-gradient(160deg,#d8d4cc,#8b8276 55%,#b8894a)" role="img" aria-label="Photo of the lounge and lockers"></div>
  <div class="shot" style="left:440px;top:162px;background:linear-gradient(160deg,#cfc9bd,#8e8a82 50%,#c9b79a)" role="img" aria-label="Photo of the print station and meeting table"></div>
  <div class="shot" style="left:771px;top:162px;background:linear-gradient(160deg,#6d6a66,#2a2826 45%,#c9a832 80%,#8e8b86)" role="img" aria-label="Photo of gaming-style desk chairs"></div>
  <div class="shot" style="left:108px;top:390px;background:linear-gradient(160deg,#4b4a45,#8a7e5e 45%,#c99a3e)" role="img" aria-label="Photo of wooden tables under pendant lamps"></div>
  <div class="shot" style="left:440px;top:390px;background:linear-gradient(160deg,#9a968e,#5b574e 50%,#b79f73)" role="img" aria-label="Photo of the glass-walled meeting room"></div>
  <div class="shot" style="left:771px;top:390px;background:linear-gradient(160deg,#b3b0ab,#6e6c6a 45%,#b38a55)" role="img" aria-label="Photo of the kitchen with steel fridge"></div>
</section>

<div class="contact-photo" role="img" aria-label="Photo of the lounge with sofas, lockers and bar stools"></div>
<section class="contact">
  <h2 class="contact-title">CONTACT US</h2>
  <div class="rule"></div>
  <div class="field" style="top:148px">Name*</div>
  <div class="field" style="top:202px">E-mail address*</div>
  <div class="field" style="top:258px">Phone*</div>
  <div class="field" style="top:313px;height:91px">Leave Message</div>
  <a class="btn">SEND</a>
</section>

<footer class="site-footer">
  <nav class="footer-nav"><span>HOME</span><span>ABOUT</span><span>AMENITIES</span><span>MEMBERSHIP</span><span>PICTURES</span><span>THE DESKHAVEN PHILOSOPHY</span><span>CONTACT</span></nav>
  <p class="copyright">Copyright © 2020 Deskhaven Cospace &nbsp;|&nbsp; Privacy Policy</p>
  <div class="social"><span aria-label="Social link"></span><span aria-label="Social link"></span><span aria-label="Social link"></span></div>
</footer>

</body>
</html>
```